plomira TrendScope Sunrush2025

plomira Brand Background
Who We Are:
plomira is a next-generation marketing intelligence company. Our core platform, plomira TrendScope, delivers daily, real-time insights into what’s driving audience engagement and sales across 20,000+ brands and 15+ digital channels.

Mission
To empower brands and marketers to capture every revenue opportunity in an “Always-On Opportunity” economy—by transforming short-term market volatility into predictable, repeatable growth.

Vision
To make every marketing moment count. We envision a future where brands aren’t caught off-guard by trends, but are always the first to know, first to act, and always ahead of the curve—turning volatility into a strategic advantage.

Brand Claim / Tagline
plomira puts you ahead to see, ahead to move.

Or, shorter for slides:
First to Know. First to Act.

Creative Direction / Brand Tone (optional for designers):
Modern, bold, digital-first
Data-driven and energetic
Trusted partner to ambitious, innovative brands

One-Line Summary for Designers:

“plomira empowers retail brands with real-time, actionable marketing intelligence—so you can act faster, grow smarter, and capture the opportunities others miss.”

Target Market(s)

Retail managers CEO, CMO

Industry/Entity Type

B2C Retail

Font styles to use
Sans Serif

Colors
EB3D1F
EC4F4E
F09395
F8D3D4
FCEDEE

Requirements
Must have
• Compelling brand building and selling the “Sunrush & Yuletide Income Booster” package
Nice to have
• ^building one of the design foundations for new website design
Should not have
• unnecessary stuff, keep it clean and slim

```html
<!DOCTYPE html>
<html lang="en">
<head>
<meta charset="utf-8">
<title>plomira TrendScope Sunrush2025 – Deck Overview</title>
<link href="https://fonts.googleapis.com/css2?family=Roboto:ital,wght@0,400;0,500;0,700;1,400&display=swap" rel="stylesheet">
<style>
:root{
  --red:#c8202a;
  --red-bright:#d8262f;
  --dark:#36383c;
  --ink:#222326;
  --muted:#4a4b4f;
  --canvas:#a7a7a7;
  --paper:#f3f3f3;
  --white:#ffffff;
  --navy:#12405f;
  --navy-dark:#0b2a40;
  --orange:#d85a24;
  --orange-dark:#a8411a;
}
*{box-sizing:border-box;margin:0;padding:0}
html,body{width:1012px;height:1200px;overflow:hidden}
body{background:var(--canvas);font-family:"Roboto",Arial,sans-serif;color:var(--ink);position:relative}
.slide{position:absolute;width:800px;height:450px;overflow:hidden;transform:scale(.5737);transform-origin:0 0;
  background:linear-gradient(125deg,#ececec 0%,#f8f8f8 45%,#efefef 70%,#fafafa 100%)}
.col-l{left:31.6px}.col-r{left:520.9px}
.row-1{top:37.9px}.row-2{top:326.4px}.row-3{top:615.6px}.row-4{top:904.2px}
.a{position:absolute}
.chrome{position:absolute;left:0;top:0;width:800px;height:450px}
.logo{position:absolute;left:56px;top:14px;font-size:29px;font-weight:500;color:var(--dark);letter-spacing:.5px;display:flex;align-items:center;gap:6px}
.logo .dot{width:10px;height:10px;border-radius:50%;background:var(--red)}
.slide-title{position:absolute;right:56px;top:17px;color:var(--white);font-size:23px;font-weight:700}
.footer-copy{position:absolute;left:56px;top:430px;font-size:10px;color:var(--white)}
.footer-page{position:absolute;left:688px;top:430px;font-size:10px;color:var(--white)}
.center{text-align:center;left:0;width:800px}
/* cover */
.cover-head{left:57px;top:146px;color:var(--white);font-size:24px;font-weight:700;line-height:30px}
.cover-rule{left:57px;top:217px;width:250px;height:2px;background:var(--white)}
.cover-sub{left:57px;top:228px;color:var(--white);font-size:16px;font-weight:700;line-height:21px}
.cover-copy{left:57px;top:419px;font-size:7px;color:var(--ink)}
/* planning cards */
.plan-card{top:108px;width:331px;height:283px;background:var(--white);border-radius:10px;box-shadow:0 2px 10px rgba(0,0,0,.06)}
.plan-pill{position:absolute;left:22px;top:9px;width:287px;height:33px;border-radius:5px;background:var(--red);color:var(--white);font-size:14px;font-weight:700;display:flex;align-items:center;justify-content:center}
.plan-item{position:absolute;left:22px;width:287px;padding-left:52px}
.plan-item+.plan-item{border-top:1px solid #dedede}
.plan-num{position:absolute;left:16px;top:0;font-size:20px;font-weight:700;color:var(--ink)}
.plan-name{color:var(--red);font-size:14px;font-weight:700;margin-bottom:5px}
.plan-text{font-size:9.5px;line-height:14.5px;color:var(--ink)}
/* about */
.about-lead{left:57px;top:86px;width:700px;font-size:14.5px;font-weight:700;line-height:25px}
.about-card{top:151px;width:221px;height:150px;background:var(--white);border-radius:10px;box-shadow:0 3px 12px rgba(0,0,0,.08);text-align:center}
.icon-badge{position:absolute;left:82px;top:14px;width:56px;height:56px;border-radius:50%;background:var(--red);display:flex;align-items:center;justify-content:center}
.about-card h3{position:absolute;top:79px;width:100%;font-size:14px;font-weight:500}
.about-card p{position:absolute;top:101px;left:28px;right:28px;font-size:8.5px;line-height:12.5px;color:var(--muted)}
.quote{top:317px;font-size:10px;font-style:italic;line-height:15px;color:var(--ink)}
.quote-by{top:357px;font-size:10px;font-weight:700}
/* flow */
.flow-lead{top:76px;font-size:14px;font-weight:700;line-height:19px}
.doc-label{top:137px;width:200px;text-align:center;font-size:10px;font-weight:500}
.doc-thumb{top:157px;width:137px;height:76px;background:linear-gradient(180deg,#ffffff,#eef1f5);border:1px solid #c9ccd2;box-shadow:2px 2px 3px rgba(0,0,0,.25)}
.step{top:285px;width:240px;text-align:center;color:var(--white)}
.step h4{font-size:15px;font-weight:700;margin-bottom:3px}
.step p{font-size:8.5px;line-height:12.5px}
/* exec */
.exec-head{top:78px;font-size:18px;font-weight:500}
.exec-h{left:58px;font-size:14.5px;font-weight:700;line-height:19px}
.bullets{left:58px;list-style:none;font-size:9.5px}
.bullets li{position:relative;padding-left:24px;line-height:19px}
.bullets li::before{content:"";position:absolute;left:0;top:5px;width:9px;height:9px;border:1.5px solid var(--red);border-radius:50%;background:radial-gradient(circle,var(--red) 0 1.6px,transparent 2px)}
.exec-q{left:420px;top:131px;width:320px;text-align:center;color:var(--red);font-size:14.5px;font-weight:700;line-height:19px}
.pie-label{top:208px;width:180px;text-align:center;font-size:12px;line-height:17px;color:var(--muted)}
/* results */
.stat{top:134px;width:162px;height:162px;border:4px solid var(--red);border-radius:50%;background:var(--white);text-align:center}
.stat b{display:block;margin-top:38px;font-size:24px;color:var(--red);font-weight:700}
.stat span{display:block;margin:10px auto 0;width:120px;font-size:8.5px;font-weight:700;line-height:12.5px}
.results-line{top:311px;font-size:14px;font-weight:700}
/* attention */
.att-lead{top:80px;font-size:14px;font-weight:700;line-height:19px}
.att-item{left:390px;width:360px;font-size:14px;line-height:19px;padding-left:42px}
.att-num{position:absolute;left:0;top:2px;width:29px;height:29px;border-radius:50%;background:var(--red);color:var(--white);font-size:13px;font-weight:700;display:flex;align-items:center;justify-content:center}
.att-close{left:392px;top:316px;width:360px;font-size:14px;line-height:19px}
/* thank you */
.thanks-photo{left:0;top:0;width:800px;height:450px;background:linear-gradient(100deg,#3b4a5c 0%,#c9c3c3 35%,#f2e9e9 50%,#c3282c 75%,#7b0f14 100%)}
.thanks-logo{left:0;width:800px;top:24px;display:flex;justify-content:center}
.thanks-logo .logo{position:static}
.thanks-title{top:80px;font-size:40px;font-weight:700;color:var(--dark)}
.thanks-title em{font-style:normal;color:var(--red)}
</style>
</head>
<body>

<!-- Cover -->
<section class="slide col-l row-1">
  <svg class="chrome" viewBox="0 0 800 450">
    <defs><linearGradient id="wedge" x1="0" x2="1"><stop offset="0" stop-color="#555759"/><stop offset=".6" stop-color="#2b2c2e"/><stop offset="1" stop-color="#1d1e20"/></linearGradient></defs>
    <polygon points="0,96 380,136 380,308 0,350" fill="url(#wedge)"/>
    <circle cx="577" cy="225" r="218" fill="var(--red)"/>
    <circle cx="577" cy="225" r="203" fill="var(--white)"/>
    <circle cx="577" cy="225" r="185" fill="var(--dark)"/>
  </svg>
  <div class="logo"><span>plomira</span><span class="dot"></span></div>
  <div class="a cover-head">First to Know.<br>First to Act.</div>
  <div class="a cover-rule"></div>
  <div class="a cover-sub">Turn Market Volatility into Growth<br>– the “Sunrush &amp; Yuletide<br>Income Booster” package</div>
  <div class="a" role="img" aria-label="Photo: white maze with a broken wall and a red ball escaping" style="left:396px;top:44px;width:362px;height:362px;border-radius:50%;background:radial-gradient(circle at 55% 40%,#f4f6fa,#c9d3e2 70%,#aab7cc)"></div>
  <div class="a cover-copy">© Copyrights 2025 | All Rights Reserved</div>
</section>

<!-- Page 05 -->
<section class="slide col-r row-1">
  <svg class="chrome" viewBox="0 0 800 450">
    <polygon points="230,0 300,62 800,62 800,0" fill="var(--red)"/>
    <polygon points="252,0 318,62 800,62 800,0" fill="var(--dark)"/>
    <rect x="0" y="421" width="800" height="29" fill="var(--dark)"/>
    <polygon points="640,421 800,421 800,450 666,450" fill="var(--red)"/>
  </svg>
  <div class="logo"><span>plomira</span><span class="dot"></span></div>
  <div class="slide-title">From Reactive to Pro-active</div>
  <div class="a center" style="top:78px;font-size:14px;font-weight:500">Turn Volatility into Growth</div>
  <div class="a plan-card" style="left:56px">
    <div class="plan-pill">Traditional Planning</div>
    <div class="plan-item" style="top:54px;height:74px"><span class="plan-num">01</span><div class="plan-name">Internal Signals</div><div class="plan-text">Weekly tweaks to annual roadmap; few real-time signals from hypes, competitors, events. Manual ex-post competitor screening.</div></div>
    <div class="plan-item" style="top:135px;height:74px;padding-top:8px"><span class="plan-num" style="top:8px">02</span><div class="plan-name">Manual Orchestration</div><div class="plan-text">Break campaigns into messages by hand. Cross-channel coordination depends on complex sync and sign-of.</div></div>
    <div class="plan-item" style="top:216px;height:60px;padding-top:8px"><span class="plan-num" style="top:8px">03</span><div class="plan-name">Speed: Weeks</div><div class="plan-text">Yearly master plan, monthly sprints, weekly refinements.</div></div>
  </div>
  <div class="a plan-card" style="left:413px">
    <div class="plan-pill">Always-On Opportunity Capture</div>
    <div class="plan-item" style="top:54px;height:74px"><span class="plan-num">01</span><div class="plan-name">360° Signals</div><div class="plan-text">Plan + audience sentiment + trends + competitors +upcoming events. Overnight scans = fresh insight briefs by morning.</div></div>
    <div class="plan-item" style="top:135px;height:64px;padding-top:8px"><span class="plan-num" style="top:8px">02</span><div class="plan-name">Auto-orchestrated planning</div><div class="plan-text">Campaign building and channels mapping. Daily re-calibration based on live performance.</div></div>
    <div class="plan-item" style="top:208px;height:70px;padding-top:8px"><span class="plan-num" style="top:8px">03</span><div class="plan-name">Speed: Days</div><div class="plan-text">2-Day fast-lane activities addressing market volatility &amp; short-term opportunities. Automated 10-day / 70-day mid-term updates.</div></div>
  </div>
  <div class="footer-copy">© Copyrights 2025 | All Rights Reserved</div>
  <div class="footer-page">Page No : 05</div>
</section>

<!-- Page 02 -->
<section class="slide col-l row-2">
  <svg class="chrome" viewBox="0 0 800 450">
    <polygon points="230,0 300,62 800,62 800,0" fill="var(--red)"/>
    <polygon points="252,0 318,62 800,62 800,0" fill="var(--dark)"/>
    <rect x="0" y="421" width="800" height="29" fill="var(--dark)"/>
    <polygon points="640,421 800,421 800,450 666,450" fill="var(--red)"/>
  </svg>
  <div class="logo"><span>plomira</span><span class="dot"></span></div>
  <div class="slide-title">About plomira</div>
  <div class="a about-lead">We live in an #AlwaysOnOpportunity economy, where market volatility is the only constant.&nbsp; 60% of revenue opportunities now occur outside of planned marketing campaigns.</div>
  <div class="a about-card" style="left:63px">
    <div class="icon-badge"><svg width="30" height="30" viewBox="0 0 30 30" fill="none" stroke="#fff" stroke-width="1.6"><path d="M15 5a7 7 0 0 0-4 12.7V21h8v-3.3A7 7 0 0 0 15 5z"/><path d="M12 24h6M13 27h4"/></svg></div>
    <h3>Our How</h3>
    <p>Our AI platform daily analyses 20,000+ brands across 15 channels to identify what your audience is actually interested in right now.</p>
  </div>
  <div class="a about-card" style="left:292px">
    <div class="icon-badge"><svg width="30" height="30" viewBox="0 0 30 30" fill="none" stroke="#fff" stroke-width="1.6"><rect x="7" y="4" width="16" height="22" rx="1"/><path d="M10 9h10M10 13h10M10 17h6"/><rect x="9" y="20" width="12" height="4"/></svg></div>
    <h3>Our Claim</h3>
    <p>plomira puts you ahead to see, ahead to move.</p>
  </div>
  <div class="a about-card" style="left:522px">
    <div class="icon-badge"><svg width="30" height="30" viewBox="0 0 30 30" fill="none" stroke="#fff" stroke-width="1.6"><path d="M8 24v-5M13 24v-8M18 24v-6M23 24v-11"/><path d="M6 15l6-5 5 3 8-7"/><path d="M21 6h4v4"/></svg></div>
    <h3>The Result</h3>
    <p>Brands capturing #AlwaysOnOpportunities see 2.8x higher revenue growth*)</p>
  </div>
  <div class="a center quote">“With plomira TrendScope, we were able to spot and act on new market trends days before our competitors. The speed and<br>clarity of insights transformed our clients’ Sunrush campaigns into true revenue drivers.”</div>
  <div class="a center quote-by">— Matthis Kornwald, CEO vendaro</div>
  <div class="footer-copy">© Copyrights 2025 | All Rights Reserved</div>
  <div class="footer-page">Page No : 02</div>
</section>

<!-- Page 06 -->
<section class="slide col-r row-2">
  <svg class="chrome" viewBox="0 0 800 450">
    <polygon points="230,0 300,62 800,62 800,0" fill="var(--red)"/>
    <polygon points="252,0 318,62 800,62 800,0" fill="var(--dark)"/>
    <rect x="0" y="421" width="800" height="29" fill="var(--dark)"/>
    <polygon points="640,421 800,421 800,450 666,450" fill="var(--red)"/>
    <polygon points="56,271 262,271 298,311 262,352 56,352" fill="var(--red)"/>
    <polygon points="280,271 484,271 520,311 484,352 280,352 316,311" fill="var(--red)"/>
    <polygon points="502,271 708,271 744,311 708,352 502,352 538,311" fill="var(--red)"/>
  </svg>
  <div class="logo"><span>plomira</span><span class="dot"></span></div>
  <div class="slide-title">How #AlwaysOnOpportunity drives Growth</div>
  <div class="a center flow-lead">Always-On Opportunity Capture ensures your messaging maintains timely and<br>Continuous Relevance with your audience.</div>
  <div class="a doc-label" style="left:28px">Market Forensics</div>
  <div class="a doc-label" style="left:300px">Prioritise Opportunities</div>
  <div class="a doc-label" style="left:572px">Campaign Planning</div>
  <div class="a doc-thumb" role="img" aria-label="Sample market forensics report page" style="left:60px"></div>
  <div class="a doc-thumb" role="img" aria-label="Sample opportunity priority table" style="left:332px"></div>
  <div class="a doc-thumb" role="img" aria-label="Sample campaign planning calendar" style="left:612px"></div>
  <div class="a step" style="left:50px;width:230px"><h4>Spot</h4><p>Detect a rising „mother-daughter<br>fashion“ trend on ClipNest.</p></div>
  <div class="a step" style="left:290px;width:230px"><h4>Validate</h4><p>High-potential, low-competition angle<br>for my brand.</p></div>
  <div class="a step" style="left:513px;width:240px"><h4>Act</h4><p>Suggest a 5-day campaign across ClipNest,<br>Snapvue, Circlebook</p></div>
  <div class="footer-copy">© Copyrights 2025 | All Rights Reserved</div>
  <div class="footer-page">Page No : 06</div>
</section>

<!-- Page 03 -->
<section class="slide col-l row-3">
  <svg class="chrome" viewBox="0 0 800 450">
    <polygon points="230,0 300,62 800,62 800,0" fill="var(--red)"/>
    <polygon points="252,0 318,62 800,62 800,0" fill="var(--dark)"/>
    <rect x="0" y="421" width="800" height="29" fill="var(--dark)"/>
    <polygon points="640,421 800,421 800,450 666,450" fill="var(--red)"/>
    <!-- pie -->
    <path d="M464,313 L464,333 A113,50 0 0 0 690,333 L690,313 A113,50 0 0 1 464,313 Z" fill="var(--navy-dark)"/>
    <path d="M464,313 L464,333 A113,50 0 0 0 510.6,373.5 L510.6,353.5 A113,50 0 0 1 464,313 Z" fill="var(--orange-dark)"/>
    <path d="M577,313 L577,263 A113,50 0 1 1 510.6,353.5 Z" fill="var(--navy)"/>
    <path d="M577,313 L510.6,353.5 A113,50 0 0 1 577,263 Z" fill="var(--orange)"/>
  </svg>
  <div class="logo"><span>plomira</span><span class="dot"></span></div>
  <div class="slide-title">Executive Summary</div>
  <div class="a center exec-head">60% of Opportunities are missed</div>
  <div class="a exec-h" style="top:113px">Key Business Impact of<br>#AlwaysOnOpportunity capture:</div>
  <ul class="a bullets" style="top:167px">
    <li>10-15% higher conversion rates</li>
    <li>15-20% increase in audience engagement</li>
    <li>20-25% higher marketing team effectiveness</li>
    <li>up to 2.8x higher revenue growth</li>
  </ul>
  <div class="a exec-h" style="top:266px">Avoid the cost of inaction, get prepared for<br>Sunrush &amp; Yuletide 2025</div>
  <ul class="a bullets" style="top:313px;width:330px">
    <li>Timeline to Value: operational within 6 weeks,</li>
    <li>Investment: 2-3 of your marketing experts, 15.000 € for plomira platform &amp; support,</li>
    <li>Expected results: +5..10% revenue.</li>
  </ul>
  <div class="a exec-q">Often, marketing is capturing less than 40% of potential business. What if you could capture the other 60%?</div>
  <div class="a pie-label" style="left:380px">Planned<br>Marketing: 40%</div>
  <div class="a pie-label" style="left:578px;color:var(--ink);font-weight:700">Unplanned<br>Opportunities: 60%</div>
  <div class="footer-copy">© Copyrights 2025 | All Rights Reserved</div>
  <div class="footer-page">Page No : 03</div>
</section>

<!-- Page 07 -->
<section class="slide col-r row-3">
  <svg class="chrome" viewBox="0 0 800 450">
    <polygon points="230,0 300,62 800,62 800,0" fill="var(--red)"/>
    <polygon points="252,0 318,62 800,62 800,0" fill="var(--dark)"/>
    <rect x="0" y="421" width="800" height="29" fill="var(--dark)"/>
    <polygon points="640,421 800,421 800,450 666,450" fill="var(--red)"/>
  </svg>
  <div class="logo"><span>plomira</span><span class="dot"></span></div>
  <div class="slide-title">Results through #AlwaysOnOpportunity</div>
  <div class="a stat" style="left:57px"><b>3X</b><span>3x faster*) trend identification: First-Mover advantage.</span></div>
  <div class="a stat" style="left:233px"><b>10 - 15%</b><span>Higher conversion rates through Gap-First ideation.</span></div>
  <div class="a stat" style="left:408px"><b>15 - 20%</b><span>Increase in audience engagement = larger qualified pipeline &amp; higher Lifetime Value.</span></div>
  <div class="a stat" style="left:583px"><b>20 - 25%</b><span>Higher marketing team effectiveness = 2-3 free specialists.</span></div>
  <div class="a center results-line">Leaders’ revenue grows 2.8x faster*) than trailing brands.</div>
  <div class="footer-copy">© Copyrights 2025 | All Rights Reserved</div>
  <div class="footer-page">Page No : 07</div>
</section>

<!-- Page 04 -->
<section class="slide col-l row-4">
  <svg class="chrome" viewBox="0 0 800 450">
    <polygon points="230,0 300,62 800,62 800,0" fill="var(--red)"/>
    <polygon points="252,0 318,62 800,62 800,0" fill="var(--dark)"/>
    <rect x="0" y="421" width="800" height="29" fill="var(--dark)"/>
    <polygon points="640,421 800,421 800,450 666,450" fill="var(--red)"/>
    <circle cx="224" cy="256" r="136" fill="var(--red)"/>
    <circle cx="224" cy="256" r="122" fill="var(--white)"/>
    <circle cx="224" cy="256" r="112" fill="var(--dark)"/>
  </svg>
  <div class="logo"><span>plomira</span><span class="dot"></span></div>
  <div class="slide-title">Attention is now the #1 Line-Item Cost</div>
  <div class="a center att-lead">Marketing Reality Check: Attention costs are skyrocketing – Generating qualified leads at<br>scale cost 3x more than 2020.</div>
  <div class="a" role="img" aria-label="Photo: business presenter standing in a modern office beside a whiteboard" style="left:114px;top:146px;width:220px;height:220px;border-radius:50%;background:radial-gradient(circle at 50% 45%,#dfe3e6,#9aa5ad 70%,#5e6870)"></div>
  <div class="a att-item" style="top:150px"><span class="att-num">01</span>Incomplete cross-channel messaging reaches only 20% of your potential Audience.</div>
  <div class="a att-item" style="top:206px"><span class="att-num">02</span>Fragmented storytelling does not fit with current audience Interest.</div>
  <div class="a att-item" style="top:263px"><span class="att-num">03</span>80% of audience is not in “Buy-Now” mode when your campaign hits.</div>
  <div class="a att-close">Reacting to market dynamics (instead of driving them) leads to lost revenue, missed new customers, higher marketing cost.</div>
  <div class="footer-copy">© Copyrights 2025 | All Rights Reserved</div>
  <div class="footer-page">Page No : 04</div>
</section>

<!-- Thank you -->
<section class="slide col-r row-4">
  <div class="a thanks-photo" role="img" aria-label="Photo: business handshake over a red city skyline with network lines and rising chart"></div>
  <div class="a thanks-logo"><div class="logo"><span>plomira</span><span class="dot"></span></div></div>
  <div class="a center thanks-title">Thank <em>You</em></div>
</section>

</body>
</html>
```